Recruitment of Trellan Staffing for the UK market

I want a website for the UK market to attract businesses and companies to come to us for Philipine labour. We want an information site that gives all information on what we do and how we can recruit Philippine labour.
This is a recruitment site for companies to contact us with their requirements for skilled workers coming from the Philipines over to the UK to work.

Target Market(s)

Uk Companies and businesses who want Philipine skilled workers

Industry/Entity Type

REcruitment

Coding

Number of Pages Required

5+ page

Font styles to use
Sans Serif

Colors
0054AA
0677BA
7BADD7
CADEEF
E8F1F8
0094D4
00A9DD
6FCCEA
C7EBF8
E9F6FB
EE7325
F08F49
F5BC92
FAE3D3
FDF4ED
EB3D1F
EC4F4E
F09395
F8D3D4
FCEDEE

Requirements
Must have
• Look professional and corperate with drop down menus for Home ,about, services,articles. training , contact us
Nice to have
• Look at Velmora recruitment- https://velmorarecruitment.example.co.uk/. This is my current site - https://www.trellanstaffing.example.com/
Should not have
• Cartoons or silly pictures , needs to be corperate looking

```html
<!DOCTYPE html>
<html lang="en">
<head>
<meta charset="utf-8">
<title>Trellan Staffing – Skilled Philippine Workers for UK Companies</title>
<link href="https://fonts.googleapis.com/css2?family=Nunito+Sans:wght@400;600;700;800&display=swap" rel="stylesheet">
<style>
:root{
  --brand:#9b3631;
  --ink:#111111;
  --body:#444444;
  --muted:#666666;
  --line:#d6d6d6;
  --paper:#ffffff;
  --tint:#f4f2f2;
}
*{box-sizing:border-box;margin:0;padding:0}
html,body{width:1200px;height:3584px;overflow:hidden}
body{position:relative;background:var(--paper);font-family:"Nunito Sans",Arial,sans-serif;color:var(--ink)}
.abs{position:absolute}
a{color:inherit;text-decoration:none}

/* header */
.brand-name{left:135px;top:48px;font-size:34px;font-weight:800;color:var(--brand);letter-spacing:.5px}
.contact-chip{display:flex;align-items:center;gap:12px}
.chip-icon{width:36px;height:36px;border-radius:50%;background:var(--brand);display:flex;align-items:center;justify-content:center}
.chip-label{font-size:11px;color:var(--body);text-transform:uppercase}
.chip-value{font-size:17px;color:var(--ink)}
.nav{left:555px;top:84px;display:flex;gap:32px;font-size:13px;text-transform:uppercase}
.nav a.active{color:var(--brand);font-weight:700;border-bottom:2px solid var(--brand);padding-bottom:8px}

/* hero */
.hero-title{left:134px;top:248px;font-size:39px;line-height:53px;font-weight:800}
.hero-title .accent{color:var(--brand)}
.btn-solid{background:var(--brand);color:#fff;font-weight:800;font-size:14px;text-transform:uppercase;display:flex;align-items:center;justify-content:center}
.hero-rule{left:543px;top:136px;width:2px;height:553px;background:var(--line)}
.hero-photo{left:551px;top:140px;width:517px;height:546px;background:linear-gradient(160deg,#d8d3ca 0%,#b7aa98 40%,#6c5f52 100%)}

/* intro */
.eyebrow{left:0;width:1200px;top:766px;text-align:center}
.eyebrow span{display:inline-block;font-size:18px;font-weight:800;color:var(--brand);border-top:2px solid var(--brand);border-bottom:2px solid var(--brand);padding:6px 2px}
.intro{left:250px;width:700px;top:833px;text-align:center;font-size:19px;line-height:31px;font-weight:800}

.card{border:1px solid var(--line);background:#fff;width:450px;height:276px}
.card-icon{left:32px;top:39px;width:72px;height:72px;border-radius:50%;background:var(--brand);display:flex;align-items:center;justify-content:center}
.card-title{left:134px;top:34px;font-size:14px;font-weight:800}
.card-text{left:134px;top:64px;width:278px;font-size:12.4px;line-height:19.2px;color:var(--body);text-align:justify}

/* about band */
.band-photo{left:0;top:1575px;width:1200px;height:537px;background:linear-gradient(100deg,#6a4a2c 0%,#3b2e25 40%,#8a7560 60%,#2a1f1a 100%)}
.band-box{left:132px;top:1978px;width:936px;height:134px;background:#fff}
.band-title{left:53px;top:62px;font-size:20px;font-weight:800;transform:translateY(-50%)}
.band-rule{left:366px;top:28px;width:2px;height:78px;background:var(--brand)}
.band-text{left:408px;top:40px;width:490px;font-size:12.4px;line-height:19px;color:var(--body)}

/* articles */
.section-rule{height:2px;background:var(--brand)}
.section-title{left:0;width:1200px;top:2210px;text-align:center;font-size:20px;font-weight:800}
.article{width:250px;top:2300px}
.article h3{font-size:18px;line-height:26px;font-weight:400;color:var(--ink)}
.article p{margin-top:20px;font-size:12.4px;line-height:19px;color:var(--body)}
.btn-small{margin-top:20px;width:81px;height:28px;font-size:9px}
.col-rule{top:2301px;width:1px;height:218px;background:#888}
.btn-outline{left:524px;top:2576px;width:152px;height:41px;border:2px solid var(--brand);color:var(--brand);font-size:14px;font-weight:700;text-transform:uppercase;display:flex;align-items:center;justify-content:center}

/* training */
.training-bg{left:0;top:2686px;width:1200px;height:546px;background:var(--tint)}
.training-photo{left:387px;top:2732px;width:681px;height:452px;background:linear-gradient(120deg,#2b2a2c 0%,#4d3f36 45%,#7b6a5a 70%,#2d3440 100%)}
.training-box{left:138px;top:2794px;width:333px;height:390px;background:var(--brand);color:#fff}
.training-box h2{position:absolute;left:37px;top:50px;font-size:20px;font-weight:800;border-bottom:2px solid #fff;padding-bottom:4px}
.training-box p{position:absolute;left:37px;top:118px;width:240px;font-size:13px;line-height:19px;text-align:justify}
.btn-white{position:absolute;left:39px;top:312px;width:116px;height:40px;background:#fff;color:var(--brand);font-size:14px;font-weight:800;text-transform:uppercase;display:flex;align-items:center;justify-content:center}

/* footer */
.foot-logo{left:135px;top:3353px;font-size:30px;font-weight:800;color:var(--brand)}
.foot-head{font-size:14px;font-weight:800;text-transform:uppercase;padding-bottom:12px;border-bottom:2px solid var(--line)}
.foot-item{display:flex;gap:14px;align-items:flex-start;font-size:12.4px;line-height:16px;color:var(--body)}
.foot-dot{flex:none;width:22px;height:22px;border-radius:50%;background:var(--brand);display:flex;align-items:center;justify-content:center;margin-top:2px}
.foot-menu{left:744px;top:3322px;font-size:12.4px;line-height:23.5px;color:var(--body);list-style:none}
.foot-rule{left:133px;top:3505px;width:935px;height:1px;background:var(--line)}
.copyright{left:0;width:1200px;top:3538px;text-align:center;font-size:12px;color:var(--body)}
</style>
</head>
<body>

<header>
  <div class="abs brand-name">Trellan Staffing</div>
  <div class="abs contact-chip" style="left:552px;top:24px">
    <div class="chip-icon"><svg width="18" height="14" viewBox="0 0 18 14"><rect x="1" y="1" width="16" height="12" rx="1" fill="none" stroke="#fff" stroke-width="1.6"/><path d="M1 2l8 6 8-6" fill="none" stroke="#fff" stroke-width="1.6"/></svg></div>
    <div><div class="chip-label">Email us</div><div class="chip-value">sales@trellanstaffing.example.com</div></div>
  </div>
  <div class="abs contact-chip" style="left:910px;top:24px">
    <div class="chip-icon"><svg width="18" height="18" viewBox="0 0 24 24"><path d="M6.6 10.8a15 15 0 006.6 6.6l2.2-2.2a1 1 0 011-.25 11.4 11.4 0 003.6.6 1 1 0 011 1V20a1 1 0 01-1 1A17 17 0 013 4a1 1 0 011-1h3.5a1 1 0 011 1c0 1.25.2 2.45.6 3.6a1 1 0 01-.25 1z" fill="#fff"/></svg></div>
    <div><div class="chip-label">Call us</div><div class="chip-value">07700900461</div></div>
  </div>
  <nav class="abs nav">
    <a class="active" href="#">Home</a><a href="#">About</a><a href="#">Services</a><a href="#">Articles</a><a href="#">Training</a><a href="#">Contact us</a>
  </nav>
</header>

<section class="hero">
  <h1 class="abs hero-title">Recruiting and<br>placing skilled<br><span class="accent">Philippine workers</span><br>into UK companies</h1>
  <a class="abs btn-solid" href="#" style="left:135px;top:484px;width:117px;height:42px">Read more</a>
  <div class="abs hero-rule"></div>
  <div class="abs hero-photo" role="img" aria-label="Smiling Filipino worker in a hard hat with a colleague holding a clipboard"></div>
</section>

<section class="working">
  <div class="abs eyebrow"><span>WORKING TOGETHER</span></div>
  <p class="abs intro">We recruit the finest talent available with our dedicated&nbsp; 200 strong team. Our centres are highlighted in red dots on the map.</p>

  <article class="abs card" style="left:132px;top:938px">
    <div class="abs card-icon"><svg width="34" height="34" viewBox="0 0 24 24" fill="#fff"><circle cx="12" cy="6" r="3.5"/><path d="M5 21v-5a7 7 0 0114 0v5z"/></svg></div>
    <h3 class="abs card-title">What we do</h3>
    <p class="abs card-text">Our company has been estabilished in the Philippines for over 20 years. We have mainly been recruiting philippine workers for the off shore industry in asia but since brexit and the new rules on skilled workers entering the UK we have been working with UK companies who now have chance to recruit some of the finest hard working talent from the Philippines for their companies..</p>
  </article>
  <article class="abs card" style="left:618px;top:938px">
    <div class="abs card-icon"><svg width="36" height="36" viewBox="0 0 24 24" fill="none" stroke="#fff" stroke-width="2" stroke-linecap="round" stroke-linejoin="round"><path d="M2 11l4-4 4 2 4-2 6 4"/><path d="M6 13l4 4 2-1 2 1 4-4"/></svg></div>
    <h3 class="abs card-title">How we help</h3>
    <p class="abs card-text">We work with companies to find skilled workers that meet the UK requirements for Visas and work permits. We guide you through the whole process and deliver highly trained people that add value to your business. We are here to help both the companies and the Philippino people to gain a better standard of living for their families.</p>
  </article>
  <article class="abs card" style="left:132px;top:1249px">
    <div class="abs card-icon"><svg width="30" height="36" viewBox="0 0 24 28" fill="none" stroke="#fff" stroke-width="2"><path d="M12 22s7-7 7-12a7 7 0 00-14 0c0 5 7 12 7 12z"/><circle cx="12" cy="10" r="2.5"/><ellipse cx="12" cy="25" rx="6" ry="1.6"/></svg></div>
    <h3 class="abs card-title">Where to start</h3>
    <p class="abs card-text">We need to know what your issues are and how we can understand the personnal you require , over what time frame and the number of employees you need. Once this is estabilished we start sourcing workers in the Philippines that meet your criteria while starting the process in the UK to be able to have all the documents in place to deliver your company hard working skilled individuals.</p>
  </article>
  <article class="abs card" style="left:618px;top:1249px">
    <div class="abs card-icon"><svg width="34" height="34" viewBox="0 0 24 24"><path d="M6.6 10.8a15 15 0 006.6 6.6l2.2-2.2a1 1 0 011-.25 11.4 11.4 0 003.6.6 1 1 0 011 1V20a1 1 0 01-1 1A17 17 0 013 4a1 1 0 011-1h3.5a1 1 0 011 1c0 1.25.2 2.45.6 3.6a1 1 0 01-.25 1z" fill="#fff"/></svg></div>
    <h3 class="abs card-title">Contact us today</h3>
    <p class="abs card-text">Please contact us today with your requirements , this can be care workers ,chef, welders, pipe fitters, caravan cabinet makers, medical workers. The UK list of required skills is extensive and the Philippines offersenglish speaking highly qualified hard working employees. Contact us today and make that first step to a highly motivated , quality skilled workforce.</p>
  </article>
</section>

<section class="about-band">
  <div class="abs band-photo" role="img" aria-label="Young professional smiling while working at a laptop in a warm office"></div>
  <div class="abs band-box">
    <h2 class="abs band-title">What the business is about</h2>
    <div class="abs band-rule"></div>
    <p class="abs band-text">We source skilled workers directly from the Philippines to work in the UK. With offices , training locations and specialist recruiters we can find the highest quality individuals to add value and resources to any UK buisness. We delivery quality based on vast experience over a number of years.</p>
  </div>
</section>

<section class="articles">
  <div class="abs section-rule" style="left:569px;top:2194px;width:63px"></div>
  <h2 class="abs section-title">Recent Articles</h2>
  <article class="abs article" style="left:132px">
    <h3>Lorem Ipsum is simply dummy text of the printing</h3>
    <p>It is a long established fact that a reader will be distracted by the readable content of a page when looking at its layout. The point of using Lorem Ipsum is that it has a more</p>
    <a class="btn-solid btn-small" href="#">Read more</a>
  </article>
  <div class="abs col-rule" style="left:423px"></div>
  <article class="abs article" style="left:475px">
    <h3>Lorem Ipsum is simply dummy text of the printing</h3>
    <p>It is a long established fact that a reader will be distracted by the readable content of a page when looking at its layout. The point of using Lorem Ipsum is that it has a more</p>
    <a class="btn-solid btn-small" href="#">Read more</a>
  </article>
  <div class="abs col-rule" style="left:769px"></div>
  <article class="abs article" style="left:823px">
    <h3>Lorem Ipsum is simply dummy text of the printing</h3>
    <p>It is a long established fact that a reader will be distracted by the readable content of a page when looking at its layout. The point of using Lorem Ipsum is that it has a more</p>
    <a class="btn-solid btn-small" href="#">Read more</a>
  </article>
  <a class="abs btn-outline" href="#">View all articles</a>
</section>

<section class="training">
  <div class="abs training-bg"></div>
  <div class="abs training-photo" role="img" aria-label="Two businessmen shaking hands across a meeting table in an office"></div>
  <div class="abs training-box">
    <h2>Training</h2>
    <p>At vero eos et accusamus et iusto odio dignissimos ducimus qui blanditiis praesentium voluptatum deleniti atque corrupti quos dolores et quas molestias excepturi sint occaecati cupiditate non provident, similique sunt in culpa qui officia deserunt mollitia animi, id est laborum et dolorum fuga. Et harum quidem rerum facilis est et expedita</p>
    <a class="btn-white" href="#">Read more</a>
  </div>
</section>

<footer>
  <div class="abs foot-logo">Trellan Staffing</div>

  <div class="abs" style="left:457px;top:3272px;width:193px"><div class="foot-head">Contact us</div></div>
  <div class="abs foot-item" style="left:459px;top:3328px">
    <span class="foot-dot"><svg width="10" height="12" viewBox="0 0 24 28"><path d="M12 26s9-9 9-15a9 9 0 00-18 0c0 6 9 15 9 15z" fill="#fff"/></svg></span>
    <span>Alder Gardens, Eastmoor<br>EX18 1 United Kingdom</span>
  </div>
  <div class="abs foot-item" style="left:459px;top:3378px">
    <span class="foot-dot"><svg width="10" height="10" viewBox="0 0 24 24"><path d="M6.6 10.8a15 15 0 006.6 6.6l2.2-2.2a1 1 0 011-.25 11.4 11.4 0 003.6.6 1 1 0 011 1V20a1 1 0 01-1 1A17 17 0 013 4a1 1 0 011-1h3.5a1 1 0 011 1c0 1.25.2 2.45.6 3.6a1 1 0 01-.25 1z" fill="#fff"/></svg></span>
    <span>Call Us<br>07700900461</span>
  </div>
  <div class="abs foot-item" style="left:459px;top:3431px">
    <span class="foot-dot"><svg width="10" height="8" viewBox="0 0 18 14"><rect x="0" y="0" width="18" height="14" rx="1" fill="#fff"/></svg></span>
    <span>E mail Us<br>sales@trellanstaffing.example.com</span>
  </div>

  <div class="abs" style="left:742px;top:3272px;width:107px"><div class="foot-head">Menu</div></div>
  <ul class="abs foot-menu">
    <li>Home</li><li>About</li><li>Services</li><li>Articles</li><li>Training</li><li>Contact us</li>
  </ul>

  <div class="abs" style="left:960px;top:3272px;width:108px"><div class="foot-head">Follow us</div></div>
  <div class="abs foot-item" style="left:960px;top:3332px"><span class="foot-dot"></span><span>Like us on<br>FRIENDLINE</span></div>
  <div class="abs foot-item" style="left:960px;top:3381px"><span class="foot-dot"></span><span>Follow us on<br>CHIRPER</span></div>
  <div class="abs foot-item" style="left:960px;top:3432px"><span class="foot-dot"></span><span>Follow us on<br>WORKLINK</span></div>

  <div class="abs foot-rule"></div>
  <p class="abs copyright">Copyright © 2023 All Rights Reserved</p>
</footer>

</body>
</html>
```